CREATE A BUSINESS CARD FOR A BOAT CLEANING SERVICE

WE ARE STARTING A NEW BOAT CLEANING BUSINESS. WE DIVE UNDERWATER TO CLEAN BOAT HULLS, JETTIES, UNDERWATER STRUCTURES ETC. WE ARE LOOKING FOR AN UPPERMARKET MODERN LOGO AND BUSINESS CARD AS ALOT OF OUR TARGET MARKET WILL BE HIGH END. YOU HAVE TO DESIGN A BUSINESS CARD AND LOGO SEPERATELY .
THE BUSINESS CARD DIMESNION MUST BE STANDARD SIZE.
The standard dimensions of a printed business card are 3.5 x 2 inches

Target Market(s)

UNDERWATER SERVICED

Industry/Entity Type

Business

Contact Information for Business Card

HOLLAND UNDERWATER SERVICES

Font styles to use
Serif

Colors

Designer to choose colors to be used in the design.

Requirements
Must have
• HOLLAND
Nice to have
• dark
Should not have
• more than 3 colors

```html
<!DOCTYPE html>
<html lang="en">
<head>
<meta charset="utf-8">
<title>Holland Underwater Services – Business Card</title>
<link rel="stylesheet" href="https://fonts.googleapis.com/css2?family=Open+Sans:wght@300;400;600&display=swap">
<style>
  :root {
    --page: #e9eaec;
    --card: #ffffff;
    --blue: #1f78b8;
    --blue-deep: #13609c;
    --grey: #c5c8cc;
    --text-grey: #9a9ea3;
    --text-dark: #6f7378;
    --white: #ffffff;
  }
  html, body {
    margin: 0;
    width: 1200px;
    height: 1023px;
    overflow: hidden;
    background: var(--page);
    font-family: "Open Sans", Arial, sans-serif;
  }
  .card {
    position: absolute;
    left: 100px;
    top: 226px;
    width: 1000px;
    height: 571px;
    border-radius: 22px;
    overflow: hidden;
    background: var(--card);
    box-shadow: 0 14px 40px rgba(0,0,0,0.18);
  }
  .card svg { display: block; }
  .band { fill: url(#bandFill); }
  .swoosh { fill: none; stroke: var(--grey); stroke-width: 16; }
  .swoosh-thin { fill: none; stroke: var(--grey); stroke-width: 5; opacity: .7; }
  .divider { stroke: var(--blue); stroke-width: 2; }
  .holder-name { fill: var(--white); font-size: 44px; font-weight: 600; letter-spacing: 1px; }
  .holder-role { fill: var(--white); font-size: 22px; font-weight: 300; }
  .brand-name { fill: var(--blue); font-size: 56px; font-weight: 300; letter-spacing: 16px; }
  .brand-sub { fill: var(--text-grey); font-size: 22px; font-weight: 300; letter-spacing: 6px; }
  .brand-mark { fill: var(--blue); }
  .address, .contact { fill: var(--text-grey); font-size: 21px; font-weight: 300; }
  .partner-badge { fill: var(--blue); opacity: .75; }
  .partner-name { fill: var(--blue-deep); font-size: 34px; font-weight: 600; }
  .icon { fill: none; stroke: var(--blue); stroke-width: 2; }
</style>
</head>
<body>
<div class="card">
  <svg width="1000" height="571" viewBox="0 0 1000 571">
    <defs>
      <linearGradient id="bandFill" x1="0" y1="0" x2="1" y2="1">
        <stop offset="0" stop-color="#2a86c6"/>
        <stop offset="1" stop-color="#145f9b"/>
      </linearGradient>
    </defs>

    <!-- top wave band -->
    <path class="band" d="M0,0 H1000 V185 C860,215 720,70 520,105 C320,140 170,255 0,250 Z"/>
    <path class="swoosh" d="M0,272 C170,278 320,162 520,127 C720,92 860,236 1000,207"/>
    <path class="swoosh-thin" d="M0,296 C180,300 330,190 520,152"/>

    <!-- card holder -->
    <text class="holder-name" x="935" y="82" text-anchor="end">MARCUS REED</text>
    <text class="holder-role" x="935" y="118" text-anchor="end">President</text>

    <!-- brand -->
    <rect class="brand-mark" x="70" y="322" width="34" height="34"/>
    <text class="brand-name" x="122" y="358">HOLLAND</text>
    <text class="brand-sub" x="72" y="398">UNDERWATER SERVICES</text>

    <!-- partner badges -->
    <circle class="partner-badge" cx="640" cy="370" r="30"/>
    <circle class="partner-badge" cx="738" cy="370" r="22"/>
    <text class="partner-name" x="770" y="383">HOLLAND</text>

    <line class="divider" x1="70" y1="430" x2="940" y2="430"/>

    <!-- address -->
    <text class="address" x="72" y="478">140, 318-9th Ave SW</text>
    <text class="address" x="72" y="508">Harbour City, AB T0X 1A1</text>

    <!-- contacts -->
    <text class="contact" x="900" y="478" text-anchor="end">(555) 210-4836</text>
    <text class="contact" x="900" y="508" text-anchor="end">info@hollandunderwater.com</text>
    <text class="contact" x="900" y="538" text-anchor="end">www.hollandunderwater.com</text>

    <!-- phone icon -->
    <path class="icon" d="M917,464 q-3,8 4,15 q7,7 15,4 l-3,-5 l-5,2 q-5,-3 -8,-8 l2,-5 Z"/>
    <!-- mail icon -->
    <rect class="icon" x="915" y="496" width="20" height="14"/>
    <path class="icon" d="M915,496 l10,8 l10,-8"/>
    <!-- globe icon -->
    <circle class="icon" cx="925" cy="531" r="9"/>
    <path class="icon" d="M916,531 h18 M925,522 q-6,9 0,18 q6,-9 0,-18"/>
  </svg>
</div>
</body>
</html>
```